Email Signature Design

Please design an email signature, the below is an example of our current design;
___

HARCOURT ESTATE PARTNERS PTY LTD
DOMINIC FARRADAY
Licensed Strata and Community Manager

148 Calloway Street,
BRENTWICK NSW 2041

P: 02.9374.6082 F: 9463.7820
Website: www.harcourtestate.com.au

This e-mail message and accompanying data may contain information that is confidential and private. If you are not the intended recipient, the use, dissemination, distribution or copying of this message or data is prohibited.

If you have received this e-mail in error please notify us immediately and delete all material pertaining to this e-mail. strata@harcourtestate.com.au

___

We would like to incorporate our logo and company colours, you can view the colours and feel of image at www.harcourtestate.com.au

Industry/Entity Type

It Company

Requirements
Must have
• use of logo and company colours (image)

```html
<!DOCTYPE html>
<html lang="en">
<head>
<meta charset="utf-8">
<title>Harcourt Estate Partners – Email Signature</title>
<link rel="stylesheet" href="https://fonts.googleapis.com/css2?family=Source+Sans+3:wght@400;600;700&display=swap">
<style>
  :root {
    --olive: #7f7d3a;
    --slate: #6d6e70;
    --ink: #3b3b3c;
    --rule: #d9d9d9;
    --frame: #2b2b2b;
    --paper: #ffffff;
    --backdrop: #f2f1ee;
  }
  * { margin: 0; padding: 0; box-sizing: border-box; }
  html, body {
    width: 1200px;
    height: 440px;
    overflow: hidden;
    background: var(--backdrop);
    font-family: "Source Sans 3", "Myriad Pro", Arial, sans-serif;
  }
  .signature {
    position: relative;
    width: 1200px;
    height: 440px;
    background: var(--paper);
    border: 1px solid var(--frame);
  }
  .brand {
    position: absolute;
    left: 115px;
    top: 262px;
    display: flex;
    align-items: center;
    gap: 16px;
  }
  .brand-square {
    width: 40px;
    height: 40px;
    background: var(--olive);
  }
  .brand-name {
    font-size: 31px;
    font-weight: 700;
    color: var(--olive);
    letter-spacing: 0.5px;
    white-space: nowrap;
  }
  .divider {
    position: absolute;
    left: 635px;
    top: 59px;
    width: 1px;
    height: 327px;
    background: var(--rule);
  }
  .details {
    position: absolute;
    left: 667px;
    top: 64px;
    white-space: nowrap;
  }
  .person-name {
    font-size: 23px;
    font-weight: 700;
    color: var(--olive);
    line-height: 28px;
  }
  .person-role {
    font-size: 22px;
    color: var(--slate);
    line-height: 30px;
    margin-top: 4px;
  }
  .company-name {
    font-size: 22px;
    color: var(--olive);
    line-height: 30px;
    margin-top: 24px;
  }
  .company-address {
    font-size: 22px;
    color: var(--ink);
    line-height: 30px;
    margin-top: 3px;
  }
  .contact-list {
    list-style: none;
    margin-top: 27px;
  }
  .contact-item {
    display: flex;
    align-items: center;
    gap: 12px;
    font-size: 22px;
    color: var(--ink);
    line-height: 34.5px;
  }
  .contact-icon {
    width: 19px;
    height: 19px;
    flex: none;
    color: var(--slate);
  }
</style>
</head>
<body>
  <main class="signature">
    <div class="brand">
      <span class="brand-square"></span>
      <span class="brand-name">HARCOURT ESTATE PARTNERS</span>
    </div>

    <div class="divider"></div>

    <section class="details">
      <p class="person-name">DOMINIC FARRADAY</p>
      <p class="person-role">Licensed Strata and Community Manager</p>
      <p class="company-name">HARCOURT ESTATE PARTNERS PTY LTD</p>
      <p class="company-address">148 Calloway Street, BRENTWICK NSW 2041</p>

      <ul class="contact-list">
        <li class="contact-item">
          <svg class="contact-icon" viewBox="0 0 20 20" aria-hidden="true">
            <circle cx="10" cy="10" r="8.8" fill="none" stroke="currentColor" stroke-width="1.4"/>
            <path d="M7 5.5c-1.3 1-1.4 3 .2 5.5s3.6 3.6 5.2 3.2l1-1.4-2-1.6-1 .8c-.8-.4-1.7-1.5-2.1-2.4l.8-1L8.4 5z" fill="currentColor"/>
          </svg>
          <span>02.9374.6082</span>
        </li>
        <li class="contact-item">
          <svg class="contact-icon" viewBox="0 0 20 20" aria-hidden="true">
            <rect x="5" y="2.5" width="10" height="5" fill="currentColor"/>
            <rect x="1.5" y="7.5" width="17" height="8" rx="1.5" fill="currentColor"/>
            <rect x="5" y="12.5" width="10" height="5" fill="#fff" stroke="currentColor" stroke-width="1.4"/>
          </svg>
          <span>9463.7820</span>
        </li>
        <li class="contact-item">
          <svg class="contact-icon" viewBox="0 0 20 20" aria-hidden="true">
            <path d="M1.5 8 10 3l8.5 5v9h-17z" fill="currentColor"/>
            <path d="M1.5 8 10 13l8.5-5" fill="none" stroke="#fff" stroke-width="1.2"/>
          </svg>
          <span>strata@harcourtestate.com.au</span>
        </li>
        <li class="contact-item">
          <svg class="contact-icon" viewBox="0 0 20 20" aria-hidden="true">
            <g fill="none" stroke="currentColor" stroke-width="1.3">
              <circle cx="10" cy="10" r="8.3"/>
              <ellipse cx="10" cy="10" rx="3.8" ry="8.3"/>
              <path d="M1.7 10h16.6M3 5.8h14M3 14.2h14M10 1.7v16.6"/>
            </g>
          </svg>
          <span>www.harcourtestate.com.au</span>
        </li>
      </ul>
    </section>
  </main>
</body>
</html>
```